Business Card Design

New business card design

Target Market(s)

Residential & Commercial Property Managers

Industry/Entity Type

Plumbing Services

Contact Information for Business Card

Name - Rowan Keddle, title - Director, Phone Number - 0431 286 517, email - rowan@tbk-plumbing.com.au, Company ABN - 73 215 904 386,

Font styles to use
Sans Serif

Colors
0054AA
0677BA
7BADD7
CADEEF
E8F1F8

```html
<!DOCTYPE html>
<html lang="en">
<head>
<meta charset="utf-8">
<title>TBK Plumbing Services – Business Card</title>
<link rel="stylesheet" href="https://fonts.googleapis.com/css2?family=Arimo:wght@400;700&display=swap">
<style>
  :root {
    --backdrop: #ececec;
    --paper: #ffffff;
    --ink-dark: #1e2329;
    --brand-blue: #0ea3e4;
    --brand-blue-deep: #0a8cc8;
    --text-grey: #6b6f74;
    --text-light: #f2f4f6;
  }
  * { margin: 0; padding: 0; box-sizing: border-box; }
  html, body {
    width: 1200px; height: 900px; overflow: hidden;
    background: var(--backdrop);
    font-family: "Arimo", Arial, sans-serif;
  }
  .sheet {
    width: 1200px; height: 900px;
    display: flex; flex-direction: column;
    align-items: center; justify-content: center; gap: 60px;
  }
  .card {
    position: relative;
    width: 630px; height: 360px;
    border-radius: 26px;
    overflow: hidden;
    box-shadow: 0 10px 24px rgba(0,0,0,0.18);
  }
  .card-front {
    background: var(--paper);
    border: 4px solid var(--brand-blue);
  }
  .card-front .wave { position: absolute; inset: 0; width: 100%; height: 100%; }
  .wave .dark-band { fill: var(--ink-dark); }
  .wave .blue-band { fill: var(--brand-blue); }
  .wave .blue-line { fill: none; stroke: var(--brand-blue); stroke-width: 3; }

  .company-name {
    position: absolute; left: 40px; top: 26px;
    display: flex; align-items: center; gap: 10px;
    color: var(--ink-dark);
    font-weight: 400;
  }
  .company-name .wordmark { font-size: 72px; line-height: 1; letter-spacing: 2px; }
  .company-name .dot {
    width: 14px; height: 14px; border-radius: 50%;
    background: var(--brand-blue); margin-top: 30px;
  }
  .company-tagline {
    position: absolute; left: 44px; top: 108px;
    font-size: 10px; letter-spacing: 6px;
    color: var(--text-grey);
  }

  .person {
    position: absolute; right: 40px; top: 120px;
    text-align: right;
  }
  .person-name {
    font-size: 22px; font-weight: 700; color: var(--brand-blue);
    text-transform: uppercase; letter-spacing: 0.5px;
  }
  .person-title { font-size: 15px; color: var(--text-grey); margin-top: 2px; }

  .contact {
    position: absolute; right: 36px; bottom: 22px;
    list-style: none; text-align: right;
    color: var(--text-light); font-size: 16px; line-height: 26px;
  }
  .contact li { display: flex; justify-content: flex-end; align-items: center; gap: 8px; }
  .contact .label { color: var(--brand-blue); }
  .contact svg { width: 15px; height: 15px; fill: var(--brand-blue); }

  .card-back {
    background: linear-gradient(135deg, #0a98d6 0%, #0ea9ea 60%, #3cbdf0 100%);
  }
</style>
</head>
<body>
<main class="sheet">
  <section class="card card-front">
    <svg class="wave" viewBox="0 0 630 360" preserveAspectRatio="none" aria-hidden="true">
      <path class="blue-band" d="M0,180 C160,150 280,300 630,232 L630,246 C290,312 160,168 0,196 Z"/>
      <path class="blue-line" d="M40,168 C170,140 300,270 600,214"/>
      <path class="dark-band" d="M0,196 C160,168 290,312 630,246 L630,360 L0,360 Z"/>
    </svg>

    <div class="company-name">
      <span class="wordmark">tbk</span>
      <span class="dot"></span>
    </div>
    <p class="company-tagline">plumbing services</p>

    <div class="person">
      <p class="person-name">Rowan Keddle</p>
      <p class="person-title">Director</p>
    </div>

    <ul class="contact">
      <li><span><span class="label">ABN:</span> 73 215 904 386</span></li>
      <li>0431 286 517
        <svg viewBox="0 0 24 24" aria-hidden="true"><path d="M6.6 10.8a15 15 0 0 0 6.6 6.6l2.2-2.2a1 1 0 0 1 1-.25 11.4 11.4 0 0 0 3.6.57 1 1 0 0 1 1 1V20a1 1 0 0 1-1 1A17 17 0 0 1 3 4a1 1 0 0 1 1-1h3.5a1 1 0 0 1 1 1c0 1.25.2 2.45.57 3.6a1 1 0 0 1-.25 1z"/></svg>
      </li>
      <li>rowan@tbk-plumbing.com.au
        <svg viewBox="0 0 24 24" aria-hidden="true"><path d="M2 5h20v14H2z M4 7v.5l8 5 8-5V7l-8 5z" fill-rule="evenodd"/></svg>
      </li>
    </ul>
  </section>

  <section class="card card-back" role="img" aria-label="Card back: repeating water-drop pattern in shades of blue"></section>
</main>
</body>
</html>
```